New career and executive coaching business needs a business card design including logo

Company name: 'Bramblefield Growth Partners.' The aim of my coaching engagements is to help people improve their communication in the workplace and achieve their career goals. The process involves working with individuals to help them uncover their strengths and talents, then leverage those to improve their working lives. The Tarwick Inventory is the starting point to the process. I am after an exciting and interesting business card design (including logo)which is professional yet will still get people's attention.

Industry/Entity Type

Business

Contact Information for Business Card

Name: Malcolm Dervaney
Position: Owner
Address: 58 Quorrin Ct, Elmbridge Vic 3190
Phone: 0418923047
Website: bramblefieldgrowth.com.au
Email: malcolm@bgp.com.au

Colors
33a6d7
00a990
0355a3
3176b5

Requirements
Must have
• logo

```html
<!DOCTYPE html>
<html lang="en">
<head>
<meta charset="utf-8">
<title>Bramblefield Growth Partners – Business Card</title>
<link href="https://fonts.googleapis.com/css2?family=Open+Sans:wght@400;700&display=swap" rel="stylesheet">
<style>
  :root {
    --sky: #33a6d7;
    --teal: #00a990;
    --navy: #0355a3;
    --mid-blue: #3176b5;
    --paper: #ffffff;
    --backdrop: #e4e5e7;
  }
  * { box-sizing: border-box; margin: 0; padding: 0; }
  html, body {
    width: 1200px; height: 900px; overflow: hidden;
    background: var(--backdrop);
    font-family: "Open Sans", Arial, sans-serif;
  }
  .canvas { position: relative; width: 1200px; height: 900px; }

  .card {
    position: absolute;
    width: 580px; height: 332px;
    background: var(--paper);
    box-shadow: 0 6px 18px rgba(0,0,0,0.18);
    overflow: hidden;
  }

  /* Front */
  .card--front { left: 470px; top: 100px; }
  .brand {
    position: absolute; left: 120px; top: 120px;
    display: flex; align-items: center; gap: 22px;
  }
  .brand__dot {
    width: 84px; height: 84px; border-radius: 50%;
    background: var(--mid-blue);
    flex: none;
  }
  .brand__name {
    color: var(--navy);
    font-weight: 700;
    font-size: 24px;
    line-height: 1.15;
    letter-spacing: 1px;
    text-transform: uppercase;
  }

  /* Back */
  .card--back { left: 150px; top: 470px; }
  .card__panel { position: absolute; inset: 0; }
  .back-brand {
    position: absolute; left: 34px; top: 62px; width: 180px;
    display: flex; flex-direction: column; align-items: center; gap: 16px;
  }
  .back-brand__dot {
    width: 150px; height: 150px; border-radius: 50%;
    background: var(--mid-blue);
  }
  .back-brand__name {
    color: var(--navy); font-weight: 700; font-size: 13px;
    letter-spacing: 0.8px; text-transform: uppercase; text-align: center;
    line-height: 1.3;
  }
  .contact {
    position: absolute; right: 30px; top: 58px;
    color: var(--paper); text-align: right;
  }
  .contact__name { font-weight: 700; font-size: 20px; line-height: 1.1; }
  .contact__role { font-size: 15px; margin-bottom: 8px; }
  .contact__address { font-size: 15px; line-height: 1.3; margin-bottom: 14px; }
  .contact__line {
    display: flex; justify-content: flex-end; align-items: center; gap: 10px;
    font-size: 15px; line-height: 1.45;
  }
  .contact__icon { width: 13px; height: 13px; flex: none; }
</style>
</head>
<body>
<main class="canvas">

  <section class="card card--front" aria-label="Business card front">
    <div class="brand">
      <span class="brand__dot" aria-hidden="true"></span>
      <span class="brand__name">Bramblefield<br>Growth Partners</span>
    </div>
  </section>

  <section class="card card--back" aria-label="Business card back">
    <svg class="card__panel" viewBox="0 0 580 332" aria-hidden="true">
      <path d="M300 0 C340 110 320 240 250 332 L580 332 L580 0 Z" fill="var(--navy)"/>
    </svg>

    <div class="back-brand">
      <span class="back-brand__dot" aria-hidden="true"></span>
      <span class="back-brand__name">Bramblefield Growth Partners</span>
    </div>

    <div class="contact">
      <p class="contact__name">Malcolm Dervaney</p>
      <p class="contact__role">Owner</p>
      <p class="contact__address">58 Quorrin Ct, Elmbridge<br>Vic 3190</p>
      <p class="contact__line">0418923047
        <svg class="contact__icon" viewBox="0 0 16 16" aria-hidden="true"><path fill="#fff" d="M3.5 1l2.5 3-1.5 1.7c.9 2 2.6 3.8 4.8 4.8L11 9l3 2.5-1.3 2.6C7 14 2 9 1.5 2.6z"/></svg>
      </p>
      <p class="contact__line">malcolm@bgp.com.au
        <svg class="contact__icon" viewBox="0 0 16 16" aria-hidden="true"><rect x="1" y="3" width="14" height="10" fill="#fff"/><path d="M1 3l7 6 7-6" fill="none" stroke="var(--navy)" stroke-width="1.4"/></svg>
      </p>
      <p class="contact__line">bramblefieldgrowth.com.au
        <svg class="contact__icon" viewBox="0 0 16 16" aria-hidden="true"><circle cx="8" cy="8" r="7" fill="#fff"/><path d="M1 8h14M8 1c3 3 3 11 0 14M8 1c-3 3-3 11 0 14" fill="none" stroke="var(--navy)" stroke-width="1.1"/></svg>
      </p>
    </div>
  </section>

</main>
</body>
</html>
```